A Gallery type Web design

We are developing a Wordpress based website for a client that does design construction projects. E.g. Pools, Lobbies, Toilets, etc. The website will mainly be to showcase their past projects and the collections they have.
No programming required, we just need the designs!
A sample of what the client is looking for:
http://velmorati.it/
Pages to include:
• Home – A nice slider design to showcase selected photos
• Main Category Template
• Sub Category Template
• About us
• Contact us
Example of their Main Categories and their Sub Categories:
Collections - Granite
- Marble
- Sculpture
Projects - Private
- Public
- Commercial
- Overseas
Installation - Vanity tops
- Hall areas
- Toilets
The Main Category is to show a sample and link the user to the respective Sub Categories. The Sub Categories are to showcase all the photos they have from the category. Please leave a little space to add some text or caption for the photo.
Designs need to be mobile responsive!
I've attached their logo and some sample photos to use for mock ups. Let me know if you have any questions!

```html
<!DOCTYPE html>
<html lang="en">
<head>
<meta charset="utf-8">
<title>Terrazza Stone – Home</title>
<link rel="stylesheet" href="https://fonts.googleapis.com/css2?family=Arimo:wght@400;700&display=swap">
<style>
:root{
  --dark:#1d1b1a;
  --dark-2:#2a2827;
  --footer:#343332;
  --red:#d41a17;
  --red-tab:#cc1a0e;
  --ink:#1a1a1a;
  --body:#555555;
  --light:#eeeeee;
  --white:#ffffff;
}
*{margin:0;padding:0;box-sizing:border-box}
html,body{width:1013px;height:1200px;overflow:hidden}
body{font-family:"Arimo",Arial,sans-serif;background:var(--white);color:var(--ink);position:relative}
.site-header{position:absolute;left:0;top:0;width:1013px;height:110px;
  background:repeating-linear-gradient(45deg,var(--dark) 0 6px,var(--dark-2) 6px 8px),var(--dark);}
.brand{position:absolute;left:84px;top:38px;display:flex;align-items:center;gap:10px;color:var(--white);font-size:22px;font-weight:700;letter-spacing:.5px}
.brand-mark{width:16px;height:16px;background:var(--red)}
.call-now{position:absolute;right:84px;top:34px;font-size:21px;color:var(--white);letter-spacing:.3px}
.call-now span{color:var(--red);margin-left:6px}
.main-nav{position:absolute;right:84px;top:84px;display:flex;gap:38px;font-size:12.5px}
.main-nav a{color:var(--white);text-decoration:none;position:relative}
.main-nav a.active::after{content:"";position:absolute;left:50%;margin-left:-6px;top:19px;border:6px solid transparent;border-bottom-color:var(--white);border-top:0}
.header-rule{position:absolute;left:0;top:110px;width:1013px;height:4px;background:var(--white)}
.hero{position:absolute;left:0;top:114px;width:1013px;height:431px;
  background:
    radial-gradient(ellipse 260px 150px at 310px 330px,rgba(240,236,233,.55),rgba(240,236,233,0)),
    linear-gradient(90deg,#b7a3a8 0%,#8b8b90 10%,#5d5d62 35%,#6a6a70 55%,#45454a 75%,#9b9ba0 100%);}
.welcome{position:absolute;left:0;top:545px;width:1013px;height:240px;text-align:center}
.welcome h1{margin-top:37px;font-size:27px;font-weight:400;color:var(--red);letter-spacing:.3px}
.welcome h2{margin-top:12px;font-size:15px;font-weight:400;color:var(--ink)}
.welcome p{width:860px;margin:8px auto 0;font-size:11.4px;line-height:18.6px;color:var(--body);letter-spacing:-.1px}
.welcome p + p{margin-top:19px}
.projects{position:absolute;left:0;top:785px;width:1013px;height:332px;background:var(--light)}
.project-card{position:absolute;top:36px;width:258px;height:256px;background:linear-gradient(#ffffff,#f1f1f1);border:1px solid #e2e2e2;border-radius:8px}
.card-tab{position:absolute;left:-1px;top:19px;width:200px;height:38px;background:var(--red-tab);border-radius:0 8px 8px 0;display:flex;align-items:center;gap:10px;padding-left:9px;color:var(--white);font-size:19px;letter-spacing:.3px}
.card-photo{position:absolute;left:13px;top:71px;width:234px;height:110px}
.card-text{position:absolute;left:13px;top:193px;width:234px;font-size:11px;line-height:15px;color:var(--ink)}
.site-footer{position:absolute;left:0;top:1117px;width:1013px;height:83px;
  background:repeating-linear-gradient(45deg,var(--footer) 0 6px,#3a3938 6px 8px);color:var(--white)}
.footer-nav{position:absolute;left:86px;top:22px;font-size:11px;display:flex;gap:16px}
.footer-nav a{color:var(--white);text-decoration:none}
.copyright{position:absolute;left:85px;top:51px;font-size:11px}
.social{position:absolute;left:694px;top:33px;display:flex;gap:26px}
.social span{width:16px;height:16px;border:2px solid var(--white);border-radius:50%}
</style>
</head>
<body>
<header class="site-header">
  <div class="brand"><span class="brand-mark"></span>Terrazza Stone</div>
  <div class="call-now">Call Now<span>(865) 555 0142</span></div>
  <nav class="main-nav">
    <a class="active" href="#">Home</a>
    <a href="#">Main Category Template</a>
    <a href="#">Sub Category Template</a>
    <a href="#">About us</a>
    <a href="#">Contact us</a>
  </nav>
</header>
<div class="header-rule"></div>
<div class="hero" role="img" aria-label="Slider photo: two white pedestal basins against a grey mosaic tile wall with pink flowers"></div>

<section class="welcome">
  <h1>WELCOME TO TERRAZZA STONE</h1>
  <h2>Sed ut perspiciatis unde omnis iste natus error sit voluptatem.</h2>
  <p>Lorem ipsum dolor sit amet, consectetur adipiscing elit, sed do eiusmod tempor incididunt ut labore et dolore magna aliqua. Ut enim ad minim veniam, quis nostrud exercitation ullamco laboris nisi ut cillum dolore eu fugiat nulla pariatur. Sed ut perspiciatis unde omnis iste natus error sit voluptatem accusantium doloremque</p>
  <p>laudantium, totam rem aperiam, eaque ipsa quae ab illo inventore veritatis et quasi architecto beatae vitae dicta sunt explicabo. Nemo enim ipsam voluptatem quia voluptas sit aspernatur aut odit aut fugit, sed quia consequuntur magni dolores eos qui ratione voluptatem sequi nesciunt. Excepteur sint occaecat cupidatat non proident, sunt in culpa qui officia deserunt mollit anim id est laborum.</p>
</section>

<section class="projects">
  <article class="project-card" style="left:84px">
    <div class="card-tab"><svg width="26" height="26" viewBox="0 0 26 26"><circle cx="13" cy="13" r="11.5" fill="none" stroke="#fff" stroke-width="2"/><path d="M7 13h11M13 8l5 5-5 5" fill="none" stroke="#fff" stroke-width="2.4"/></svg>PUBLIC</div>
    <div class="card-photo" role="img" aria-label="Photo of a dark lobby with furniture and a lamp" style="background:linear-gradient(135deg,#2a2624,#6c6660 50%,#b9b3a8)"></div>
    <p class="card-text">Lorem ipsum dolor sit amet, consectetur adipiscing elit, incididunt ut labore et dolore magna aliqua.</p>
  </article>
  <article class="project-card" style="left:377px">
    <div class="card-tab"><svg width="26" height="26" viewBox="0 0 26 26"><circle cx="13" cy="13" r="11.5" fill="none" stroke="#fff" stroke-width="2"/><path d="M7 13h11M13 8l5 5-5 5" fill="none" stroke="#fff" stroke-width="2.4"/></svg>COMMERCIAL</div>
    <div class="card-photo" role="img" aria-label="Photo of white basins against a mosaic tile wall" style="background:linear-gradient(90deg,#8d8a90,#4c4c52 40%,#d9d6d6 55%,#5a5a60)"></div>
    <p class="card-text">Lorem ipsum dolor sit amet, consectetur adipiscing elit, incididunt ut labore et dolore magna aliqua.</p>
  </article>
  <article class="project-card" style="left:669px">
    <div class="card-tab"><svg width="26" height="26" viewBox="0 0 26 26"><circle cx="13" cy="13" r="11.5" fill="none" stroke="#fff" stroke-width="2"/><path d="M7 13h11M13 8l5 5-5 5" fill="none" stroke="#fff" stroke-width="2.4"/></svg>OVERSEAS</div>
    <div class="card-photo" role="img" aria-label="Photo of a fireplace with mosaic tiles, firewood and a woven bowl" style="background:linear-gradient(180deg,#3d2f28,#6b5a4e 55%,#d8cdbd)"></div>
    <p class="card-text">Lorem ipsum dolor sit amet, consectetur adipiscing elit, incididunt ut labore et dolore magna aliqua.</p>
  </article>
</section>

<footer class="site-footer">
  <nav class="footer-nav">
    <a href="#">Home</a><span>|</span>
    <a href="#">Main Category Template</a><span>|</span>
    <a href="#">Sub Category Template</a><span>|</span>
    <a href="#">About us</a><span>|</span>
    <a href="#">Contact us</a>
  </nav>
  <p class="copyright">Copyright © 2014 All Rights Reserved | Privacy Policy</p>
  <div class="social" aria-label="Social links"><span></span><span></span><span></span><span></span><span></span><span></span></div>
</footer>
</body>
</html>
```